Business card design for Virtual Assistance company

I need a business card designed for my virtual assistance company. We are a small company who services primarily C-level executive clients. The card needs to be double sided with the following contact information on the back:
Melissa Thornbury
Owner/CEO
info@rkpadvisory.net
www.rkpadvisory.net
555.302.9817

The front side should just have the company name incorporated: "RKP Advisory" and "virtual assistance"

The card should be simplistic, but eye catching and should speak to high level executives. Our primary focus areas consist of executive assistance and government contracting.

Target Market(s)

CEOs and executives

Contact Information for Business Card

see project description. phone, email, website.

Colors

Designer to choose only greyscale colors for use in the design.

```html
<!DOCTYPE html>
<html lang="en">
<head>
<meta charset="UTF-8">
<title>RKP Advisory – Business Card</title>
<link href="https://fonts.googleapis.com/css2?family=Poppins:wght@400;500;600&display=swap" rel="stylesheet">
<style>
  :root {
    --backdrop: #939397;
    --card-dark: #3d3d3f;
    --card-light: #ffffff;
    --ink: #3a3a3c;
    --muted: #b9b3c4;
    --rule: #cfcfd3;
  }
  * { margin: 0; padding: 0; box-sizing: border-box; }
  html, body { width: 960px; height: 1200px; overflow: hidden; }
  body {
    background: var(--backdrop);
    font-family: "Poppins", sans-serif;
    position: relative;
  }
  .card {
    position: absolute;
    top: 484px;
    width: 404px;
    height: 231px;
  }
  .card-front {
    left: 46px;
    background: var(--card-dark);
    display: flex;
    align-items: center;
    justify-content: center;
  }
  .brand-lockup {
    display: flex;
    flex-direction: column;
    align-items: center;
    color: var(--card-light);
  }
  .brand-front {
    display: flex;
    align-items: center;
    gap: 10px;
    font-weight: 600;
    font-size: 30px;
    line-height: 1.2;
    letter-spacing: 0.5px;
  }
  .brand-mark {
    width: 14px;
    height: 14px;
    background: currentColor;
  }
  .tagline-front {
    margin-top: 6px;
    font-weight: 600;
    font-size: 9px;
    letter-spacing: 4.2px;
    text-transform: uppercase;
    padding-left: 4px;
  }
  .card-back {
    left: 510px;
    background: var(--card-light);
  }
  .brand-back-lockup {
    position: absolute;
    left: 22px;
    top: 100px;
    width: 140px;
    text-align: center;
  }
  .brand-back {
    color: var(--ink);
    font-weight: 600;
    font-size: 17px;
    line-height: 1.2;
    letter-spacing: 0.3px;
  }
  .tagline-back {
    margin-top: 3px;
    color: var(--muted);
    font-weight: 500;
    font-size: 6px;
    letter-spacing: 2.2px;
    text-transform: uppercase;
  }
  .divider {
    position: absolute;
    left: 177px;
    top: 50px;
    width: 1px;
    height: 129px;
    background: var(--rule);
  }
  .person {
    position: absolute;
    left: 208px;
    top: 62px;
  }
  .person-name {
    color: var(--ink);
    font-weight: 600;
    font-size: 14px;
    letter-spacing: 0.6px;
    text-transform: uppercase;
    line-height: 1.1;
  }
  .person-title {
    color: var(--muted);
    font-weight: 400;
    font-size: 9px;
    letter-spacing: 0.8px;
    text-transform: uppercase;
    margin-top: 2px;
  }
  .contacts {
    position: absolute;
    left: 209px;
    top: 124px;
    list-style: none;
  }
  .contacts li {
    display: flex;
    align-items: center;
    gap: 7px;
    height: 17.5px;
    color: var(--ink);
    font-size: 9.5px;
    letter-spacing: 0.5px;
  }
  .contacts svg { width: 8px; height: 8px; fill: var(--muted); flex: none; }
</style>
</head>
<body>
  <section class="card card-front" aria-label="Card front">
    <div class="brand-lockup">
      <div class="brand-front"><span class="brand-mark"></span>RKP Advisory</div>
      <p class="tagline-front">Virtual Assistance</p>
    </div>
  </section>

  <section class="card card-back" aria-label="Card back">
    <div class="brand-back-lockup">
      <div class="brand-back">RKP Advisory</div>
      <p class="tagline-back">Virtual Assistance</p>
    </div>
    <div class="divider"></div>
    <div class="person">
      <p class="person-name">Melissa Thornbury</p>
      <p class="person-title">Owner/CEO</p>
    </div>
    <ul class="contacts">
      <li>
        <svg viewBox="0 0 10 10" aria-hidden="true"><path d="M2 0.5 L3.6 0.5 L4.2 2.8 L3.1 3.6 Q4 5.9 6.4 6.9 L7.2 5.8 L9.5 6.4 L9.5 8 Q9.5 9.5 8 9.5 Q0.5 9 0.5 2 Q0.5 0.5 2 0.5 Z"/></svg>
        555.302.9817
      </li>
      <li>
        <svg viewBox="0 0 10 10" aria-hidden="true"><path d="M0 2 H10 V8.5 H0 Z M0.6 2.4 L5 5.6 L9.4 2.4" stroke="#fff" stroke-width="0.7"/></svg>
        info@rkpadvisory.net
      </li>
      <li>
        <svg viewBox="0 0 10 10" aria-hidden="true"><circle cx="5" cy="5" r="4.6"/></svg>
        www.rkpadvisory.net
      </li>
    </ul>
  </section>
</body>
</html>
```